UI/ UX Design for ERP Software

We need a new UX/UI interface for a ERP software for property managers. Our CMMS / ERP solution is made based on responsive design technologies and is coded in PHP.
The overall UX to be similar to Tev Ulna - easy navigation, intuitive menus.

Industry/Entity Type

Property Management

Number of Pages Required

5+ page

Requirements
Must have
• Round dock buttons
Consistent icons across the application
Enough Spacing between buttons/icons/ menu
Consistent Font
Nice to have
• We would like the UX to allow the users to use the application without /minimum training.
Should not have
• we don't want anything that is classic with respect to UX

```html
<!DOCTYPE html>
<html lang="en">
<head>
<meta charset="utf-8">
<title>Estara – Active Dashboard</title>
<link href="https://fonts.googleapis.com/css2?family=Poppins:wght@400;500;600;700&family=Oswald:wght@400&family=Fira+Sans:wght@400;500&display=swap" rel="stylesheet">
<style>
:root{
  --brand:#0a6cf5;
  --brand-dark:#0450a8;
  --brand-light:#1b8cf5;
  --cyan:#04c6fb;
  --ink:#1d1f24;
  --ink-soft:#3b4048;
  --muted:#6b7280;
  --page:#f1f5f9;
  --card:#fafafa;
  --grid:#dcdfe3;
  --white:#ffffff;
  --c-sched:#0a6cf5;
  --c-comp:#8de07a;
  --c-future:#f5a05a;
  --c-wo:#3a3a40;
  --c-wodone:#8b87f0;
  --c-insp:#ef5a7a;
  --c-inspdone:#e5d55a;
}
*{box-sizing:border-box;margin:0;padding:0}
html,body{width:1200px;height:994px;overflow:hidden;background:var(--page);font-family:"Poppins",sans-serif;color:var(--ink)}
.canvas{position:relative;width:1200px;height:994px}
.topbar{position:absolute;left:0;top:0;width:1200px;height:83px;background:var(--white)}
.brand{position:absolute;left:50px;top:22px;display:flex;align-items:center;gap:8px}
.brand-mark{width:22px;height:22px;background:var(--brand)}
.brand-name{font-family:"Poppins",sans-serif;font-weight:600;font-size:28px;color:var(--brand);letter-spacing:-.5px}
.search{position:absolute;left:338px;top:25px;width:514px;height:30px;border:1px solid #d9dde2;border-radius:15px;background:#f6f7f9;font-family:"Fira Sans",sans-serif;font-size:10px;color:var(--ink-soft);padding:9px 22px}
.search svg{position:absolute;right:12px;top:7px}
.bell{position:absolute;left:875px;top:24px;width:32px;height:32px;border-radius:50%;background:#2f353d;display:flex;align-items:center;justify-content:center}
.bell-badge{position:absolute;right:-2px;top:-2px;width:10px;height:10px;border-radius:50%;background:var(--brand);color:#fff;font-size:7px;line-height:10px;text-align:center;border:1px solid #fff}
.avatar{position:absolute;left:928px;top:24px;width:32px;height:32px;border-radius:50%;background:linear-gradient(135deg,#7d8c99,#3e4954)}
.user-name{position:absolute;left:972px;top:34px;font-family:"Fira Sans",sans-serif;font-size:9.5px;color:var(--ink-soft)}
.user-caret{position:absolute;left:1044px;top:36px}
.logout{position:absolute;left:1072px;top:28px;width:70px;height:24px;border:1.5px solid var(--brand);border-radius:12px;font-size:8.5px;font-weight:500;color:var(--brand);display:flex;align-items:center;justify-content:center;gap:5px}
.nav{position:absolute;left:0;top:83px;width:1200px;height:53px;background:var(--brand-dark)}
.nav-item{position:absolute;top:0;height:53px;display:flex;align-items:center;gap:9px;font-family:"Oswald",sans-serif;font-size:14px;color:#fff;letter-spacing:-.1px}
.nav-item.active{background:var(--brand);padding:0 12px 0 8px}
.nav-item svg{fill:#fff}
.page-title{position:absolute;left:51px;top:176px;font-weight:700;font-size:24.5px;color:#2f3b4b;letter-spacing:.3px}
.page-title span{color:var(--brand)}
.stat{position:absolute;top:181px;display:flex;align-items:center}
.stat-icon{width:34px;height:34px;border-radius:50%;background:var(--brand);display:flex;align-items:center;justify-content:center;flex:none}
.stat-text{margin-left:13px;font-size:11px;line-height:15.5px;font-weight:500;color:var(--ink)}
.stat-label{font-weight:600;letter-spacing:.4px}
.divider{position:absolute;top:173px;width:1px;height:50px;background:#dfe3e8}
.panel{position:absolute;left:51px;top:263px;width:1100px;height:640px;background:var(--white);border:1px solid #e3e6ea}
.panel-head{position:absolute;left:0;top:0;width:1098px;height:59px;background:linear-gradient(90deg,#0672f5,#0a8cf7 55%,var(--cyan))}
.range-btn{position:absolute;top:12px;height:31px;border:1.5px solid #fff;color:#fff;font-size:11.5px;display:flex;align-items:center;justify-content:center;gap:8px}
.date-row{position:absolute;left:46px;top:93px;display:flex;align-items:center;gap:13px;font-size:11.5px;font-weight:500}
.date-icon{width:34px;height:34px;border-radius:50%;background:var(--brand);display:flex;align-items:center;justify-content:center}
.chart-card{position:absolute;left:46px;top:153px;width:998px;height:388px;background:var(--card);box-shadow:0 1px 4px rgba(0,0,0,.08)}
.legend{position:absolute;top:580px;left:0;width:1098px;font-size:11px;line-height:14.5px;color:var(--ink-soft)}
.legend-item{position:absolute;top:0;display:flex;gap:7px}
.legend-swatch{width:10px;height:10px;margin-top:2px;flex:none}
.footer{position:absolute;left:0;top:948px;width:1200px;text-align:center;font-size:11px;color:var(--ink-soft)}
</style>
</head>
<body>
<div class="canvas">
  <header class="topbar">
    <div class="brand"><div class="brand-mark"></div><div class="brand-name">Estara</div></div>
    <div class="search">Search
      <svg width="15" height="15" viewBox="0 0 16 16"><circle cx="6.5" cy="6.5" r="5" fill="none" stroke="#3b4048" stroke-width="1.4"/><line x1="10.3" y1="10.3" x2="14.5" y2="14.5" stroke="#3b4048" stroke-width="1.6"/></svg>
    </div>
    <div class="bell">
      <svg width="14" height="15" viewBox="0 0 14 15"><path d="M7 1a4 4 0 0 0-4 4v4L1.5 11h11L11 9V5a4 4 0 0 0-4-4z" fill="#fff"/><circle cx="7" cy="13" r="1.6" fill="#fff"/></svg>
      <div class="bell-badge">2</div>
    </div>
    <div class="avatar" role="img" aria-label="User profile photo"></div>
    <div class="user-name">Liam Kerrow</div>
    <svg class="user-caret" width="10" height="7" viewBox="0 0 10 7"><path d="M1 1l4 4 4-4" fill="none" stroke="#6b7280" stroke-width="1.3"/></svg>
    <div class="logout">Logout <svg width="7" height="5" viewBox="0 0 7 5"><path d="M1 1l2.5 2.5L6 1" fill="none" stroke="#0a6cf5" stroke-width="1.2"/></svg></div>
  </header>

  <nav class="nav">
    <div class="nav-item active" style="left:50px;width:95px"><svg width="14" height="12" viewBox="0 0 14 12"><path d="M7 1a6 6 0 0 0-6 6c0 1.7.7 3.2 1.8 4.3h8.4A6 6 0 0 0 7 1zm.6 7.2a1.2 1.2 0 1 1-1.4-1.4L9.5 4z"/></svg>Dashboard</div>
    <div class="nav-item" style="left:161px"><svg width="11" height="12" viewBox="0 0 11 12"><circle cx="5.5" cy="3.2" r="3"/><path d="M0 12c0-3.3 2.4-5 5.5-5S11 8.7 11 12z"/></svg>Customers</div>
    <div class="nav-item" style="left:256px"><svg width="14" height="12" viewBox="0 0 14 12"><path d="M7 0L0 6h2v6h4V8h2v4h4V6h2z"/></svg>Properties</div>
    <div class="nav-item" style="left:359px"><svg width="15" height="12" viewBox="0 0 15 12"><circle cx="5" cy="3" r="3"/><path d="M0 12c0-3 2-5 5-5s5 2 5 5z"/><path d="M9 6l2 2 4-4" fill="none" stroke="#fff" stroke-width="1.6"/></svg>Tenants</div>
    <div class="nav-item" style="left:444px"><svg width="13" height="10" viewBox="0 0 13 10"><path d="M0 0h13v1.5L6.5 5.5 0 1.5z"/><path d="M0 3l6.5 4L13 3v7H0z"/></svg>Contacts</div>
    <div class="nav-item" style="left:537px"><svg width="16" height="12" viewBox="0 0 16 12"><circle cx="5" cy="6" r="4.5"/><circle cx="5" cy="6" r="1.6" fill="#0450a8"/><circle cx="12.5" cy="3.5" r="3"/><circle cx="12.5" cy="3.5" r="1" fill="#0450a8"/><circle cx="12.5" cy="9.5" r="2.4"/></svg>Contractors</div>
    <div class="nav-item" style="left:641px"><svg width="16" height="11" viewBox="0 0 16 11"><circle cx="5" cy="3" r="2.8"/><circle cx="11.5" cy="3" r="2.5"/><path d="M0 11c0-3 2-4.5 5-4.5s5 1.5 5 4.5zM10.5 11c0-2-.5-3.3-1.5-4.2.7-.3 1.6-.5 2.5-.5 2.7 0 4.5 1.5 4.5 4.7z"/></svg>Employees</div>
    <div class="nav-item" style="left:749px"><svg width="10" height="12" viewBox="0 0 10 12"><path d="M0 0h6.5L10 3.5V12H0z"/><path d="M2.5 6h5M2.5 8.5h5" stroke="#0450a8" stroke-width="1"/></svg>Compliance Management</div>
    <div class="nav-item" style="left:915px"><svg width="14" height="11" viewBox="0 0 14 11"><path d="M2 0h10v7.5H2zM3.3 1.3v4.9h7.4V1.3z"/><path d="M0 8.5h14v2H0z"/></svg>Prevent Maintenance</div>
    <div class="nav-item" style="left:1063px"><svg width="15" height="12" viewBox="0 0 15 12"><circle cx="5" cy="3" r="3"/><path d="M0 12c0-3 2-5 5-5s5 2 5 5z"/><path d="M9.5 9.5l4-4" stroke="#fff" stroke-width="2"/></svg>Work Orders</div>
    <div class="nav-item" style="left:1158px"><svg width="9" height="13" viewBox="0 0 9 13"><path d="M1.5 1.5l5 5-5 5" fill="none" stroke="#fff" stroke-width="1.8"/></svg></div>
  </nav>

  <h1 class="page-title">Active <span>Dashboard</span></h1>

  <div class="stat" style="left:302px">
    <div class="stat-icon"><svg width="16" height="14" viewBox="0 0 14 12" fill="#fff"><path d="M7 0L0 6h2v6h4V8h2v4h4V6h2z"/></svg></div>
    <div class="stat-text"><div class="stat-label">PROPERTIES</div><div>3</div></div>
  </div>
  <div class="divider" style="left:435px"></div>
  <div class="stat" style="left:452px">
    <div class="stat-icon"><svg width="18" height="12" viewBox="0 0 18 12" fill="#fff"><circle cx="9" cy="3" r="2.6"/><circle cx="3.5" cy="4" r="2"/><circle cx="14.5" cy="4" r="2"/><path d="M4.5 12c0-3 2-4.8 4.5-4.8s4.5 1.8 4.5 4.8zM0 11c0-2.2 1.3-3.6 3.5-3.6.8 0 1.5.2 2 .5-.7.9-1.1 1.9-1.2 3.1zM18 11c0-2.2-1.3-3.6-3.5-3.6-.8 0-1.5.2-2 .5.7.9 1.1 1.9 1.2 3.1z"/></svg></div>
    <div class="stat-text"><div class="stat-label">TENANTS</div><div>8</div></div>
  </div>
  <div class="divider" style="left:569px"></div>
  <div class="stat" style="left:589px">
    <div class="stat-icon"><svg width="11" height="14" viewBox="0 0 10 12" fill="#fff"><path d="M0 0h6.5L10 3.5V12H0z"/><path d="M2.5 6h5M2.5 8.5h5" stroke="#0a6cf5" stroke-width="1"/></svg></div>
    <div class="stat-text"><div class="stat-label">TOTAL PROPERTIES AREA</div><div>422,000.00 sq.ft.</div></div>
  </div>
  <div class="divider" style="left:798px"></div>
  <div class="stat" style="left:818px">
    <div class="stat-icon"><svg width="11" height="14" viewBox="0 0 10 12" fill="#fff"><path d="M0 0h6.5L10 3.5V12H0z"/><path d="M2.5 6h5M2.5 8.5h5" stroke="#0a6cf5" stroke-width="1"/></svg></div>
    <div class="stat-text"><div class="stat-label">RENTED AREA</div><div>233,500.00 sq.ft.</div></div>
  </div>
  <div class="divider" style="left:980px"></div>
  <div class="stat" style="left:997px">
    <div class="stat-icon"><svg width="11" height="14" viewBox="0 0 10 12" fill="#fff"><path d="M0 0h6.5L10 3.5V12H0z"/><path d="M2.5 6h5M2.5 8.5h5" stroke="#0a6cf5" stroke-width="1"/></svg></div>
    <div class="stat-text"><div class="stat-label">VACANCIES AREA</div><div>188,500.00 sq.ft.</div></div>
  </div>

  <section class="panel">
    <div class="panel-head">
      <div class="range-btn" style="left:380px;width:116px"><svg width="10" height="10" viewBox="0 0 10 10"><circle cx="5" cy="5" r="4.2" fill="none" stroke="#fff" stroke-width="1.5"/><path d="M5 2.7V5h1.8" fill="none" stroke="#fff" stroke-width="1.2"/></svg>Last 7 days</div>
      <div class="range-btn" style="left:514px;width:116px"><svg width="10" height="10" viewBox="0 0 10 10"><circle cx="5" cy="5" r="4.2" fill="none" stroke="#fff" stroke-width="1.5"/><path d="M5 2.7V5h1.8" fill="none" stroke="#fff" stroke-width="1.2"/></svg>Last months</div>
      <div class="range-btn" style="left:648px;width:116px"><svg width="10" height="10" viewBox="0 0 10 10"><circle cx="5" cy="5" r="4.2" fill="none" stroke="#fff" stroke-width="1.5"/><path d="M5 2.7V5h1.8" fill="none" stroke="#fff" stroke-width="1.2"/></svg>Last 3 days</div>
      <div class="range-btn" style="left:782px;width:116px"><svg width="10" height="10" viewBox="0 0 10 10"><circle cx="5" cy="5" r="4.2" fill="none" stroke="#fff" stroke-width="1.5"/><path d="M5 2.7V5h1.8" fill="none" stroke="#fff" stroke-width="1.2"/></svg>Next months</div>
      <div class="range-btn" style="left:916px;width:125px"><svg width="10" height="10" viewBox="0 0 10 10"><circle cx="5" cy="5" r="4.2" fill="none" stroke="#fff" stroke-width="1.5"/><path d="M5 2.7V5h1.8" fill="none" stroke="#fff" stroke-width="1.2"/></svg>Next 3 months</div>
    </div>

    <div class="date-row">
      <div class="date-icon"><svg width="14" height="14" viewBox="0 0 14 14" fill="#fff"><path d="M1 2.5h12V13H1z"/><rect x="3" y="0.5" width="1.6" height="3"/><rect x="9.4" y="0.5" width="1.6" height="3"/><g fill="#0a6cf5"><rect x="1" y="4" width="12" height="1"/><rect x="3" y="6.5" width="2" height="1.6"/><rect x="6" y="6.5" width="2" height="1.6"/><rect x="9" y="6.5" width="2" height="1.6"/><rect x="3" y="9.5" width="2" height="1.6"/><rect x="6" y="9.5" width="2" height="1.6"/><rect x="9" y="9.5" width="2" height="1.6"/></g></svg></div>
      <span>12/27/2020 - 01/03/2021</span>
    </div>

    <div class="chart-card">
      <svg width="998" height="388" viewBox="97 416 998 388" font-family="Poppins, sans-serif" font-size="11" fill="#3b4048">
        <g stroke="var(--grid)" stroke-width="1">
          <line x1="178.5" y1="469" x2="1053" y2="469"/>
          <line x1="178.5" y1="509" x2="1053" y2="509"/>
          <line x1="178.5" y1="549" x2="1053" y2="549"/>
          <line x1="178.5" y1="590" x2="1053" y2="590"/>
          <line x1="178.5" y1="630" x2="1053" y2="630"/>
          <line x1="178.5" y1="670" x2="1053" y2="670"/>
          <line x1="178.5" y1="711" x2="1053" y2="711"/>
          <line x1="178.5" y1="456" x2="178.5" y2="741"/>
          <line x1="343.6" y1="711" x2="343.6" y2="741"/>
          <line x1="464.7" y1="711" x2="464.7" y2="741"/>
          <line x1="579.5" y1="711" x2="579.5" y2="741"/>
          <line x1="687.8" y1="711" x2="687.8" y2="741"/>
          <line x1="796.2" y1="711" x2="796.2" y2="741"/>
          <line x1="904.6" y1="711" x2="904.6" y2="741"/>
          <line x1="1025.7" y1="711" x2="1025.7" y2="741"/>
        </g>
        <g text-anchor="end">
          <text x="152" y="473">1.5</text>
          <text x="152" y="513">1.25</text>
          <text x="152" y="553">1</text>
          <text x="152" y="594">0.75</text>
          <text x="152" y="634">0.5</text>
          <text x="152" y="674">0.25</text>
          <text x="152" y="715">0</text>
        </g>
        <g text-anchor="middle">
          <text x="226" y="763">27 Dec 2020</text>
          <text x="345" y="763">28 Dec 2020</text>
          <text x="463" y="763">29 Dec 2020</text>
          <text x="579" y="763">30 Dec 2020</text>
          <text x="689" y="763">31 Dec 2020</text>
          <text x="796" y="763">01 Jan 2021</text>
          <text x="909" y="763">02 Jan 2021</text>
          <text x="1023" y="763">03 Jan 2021</text>
        </g>
        <rect x="575" y="548" width="9" height="163" fill="var(--c-sched)"/>
      </svg>
    </div>

    <div class="legend">
      <div class="legend-item" style="left:45px"><div class="legend-swatch" style="background:var(--c-sched)"></div><div>Scheduled<br>Maintenance</div></div>
      <div class="legend-item" style="left:173px"><div class="legend-swatch" style="background:var(--c-comp)"></div><div>Completed Scheduled<br>Maintenance</div></div>
      <div class="legend-item" style="left:345px"><div class="legend-swatch" style="background:var(--c-future)"></div><div>Future Scheduled<br>Maintenance</div></div>
      <div class="legend-item" style="left:491px"><div class="legend-swatch" style="background:var(--c-wo)"></div><div>Scheduled Work<br>Orders</div></div>
      <div class="legend-item" style="left:625px"><div class="legend-swatch" style="background:var(--c-wodone)"></div><div>Completed Work<br>Orders</div></div>
      <div class="legend-item" style="left:759px"><div class="legend-swatch" style="background:var(--c-insp)"></div><div>Property Inspections<br>in Progress</div></div>
      <div class="legend-item" style="left:912px"><div class="legend-swatch" style="background:var(--c-inspdone)"></div><div>Completed Property<br>Inspections</div></div>
    </div>
  </section>

  <footer class="footer">©2021 Estara, All Rights Reserved.</footer>
</div>
</body>
</html>
```